Tallow Reed Software

We are a software company selling endpoint visibility, access and security technology to enterprise-level IT departments.

Our technology helps organizations gain comprehensive visibility into and control over devices accessing their corporate network so they can quickly identify and address suspicious activity on the network that could lead to potential threats like data breaches.

This technology can cost organizations upwards of $1M - depending on the size of the organization. Our primary clients are Pinnacle 2,000 companies.

We want a professional, polished business card to represent our new brand.

Info fields to include on the card:
Name
Job Title
Office Phone #
Cell Phone #
Email address
Address: 4270 Vestridge Pond Blvd., Ste. 2600, Larkfield, MN 55812
Website address: www.tallowreedsoftware.example
Tagline: See every device. Secure the network.

Logo files and color specs document are attached. Would like color scheme to coordinate with the logo.

Also looking at stationary/envelope designs in conjunction with the business card designs. Received very few designs that included the stationary.

Software

```html
<!DOCTYPE html>
<html lang="en">
<head>
<meta charset="utf-8">
<title>Tallow Reed Software — Business Card</title>
<link rel="stylesheet" href="https://fonts.googleapis.com/css2?family=Arimo:wght@400;700&display=swap">
<style>
  :root {
    --backdrop: #e9e7e3;
    --paper: #ffffff;
    --ink: #2b2a2b;
    --ink-soft: #4a484a;
    --band-deep: #201f20;
    --on-dark: #ffffff;
  }
  * { margin: 0; padding: 0; box-sizing: border-box; }
  html, body {
    width: 1200px; height: 858px; overflow: hidden;
    background: var(--backdrop);
    font-family: "Arimo", Arial, sans-serif;
    color: var(--ink);
  }
  .canvas {
    position: relative; width: 1200px; height: 858px;
    display: flex; align-items: center; justify-content: center; gap: 60px;
  }
  .card {
    position: relative; width: 525px; height: 300px;
    background: var(--paper); overflow: hidden;
    box-shadow: 0 6px 18px rgba(0,0,0,.18);
  }

  /* Shared brand lockup */
  .brand { display: flex; align-items: center; gap: 12px; }
  .brand-dot {
    width: 16px; height: 16px; border-radius: 50%;
    background: var(--ink); flex: none;
  }
  .brand-name {
    font-weight: 700; font-size: 21px; letter-spacing: 1.5px;
    text-transform: uppercase; color: var(--ink); line-height: 1.15;
  }

  /* Front */
  .front-swoosh { position: absolute; inset: 0; width: 100%; height: 100%; }
  .front .brand { position: absolute; left: 34px; top: 58px; width: 230px; }
  .contact {
    position: absolute; right: 26px; top: 40px;
    list-style: none; font-size: 13px; line-height: 22px; color: var(--ink);
  }
  .contact li { display: flex; justify-content: flex-end; align-items: center; gap: 8px; }
  .contact svg { width: 12px; height: 12px; flex: none; fill: var(--ink); }
  .person { position: absolute; left: 30px; bottom: 18px; color: var(--on-dark); }
  .person-name { font-size: 20px; line-height: 1.15; }
  .person-title { font-size: 15px; line-height: 1.3; }

  /* Back */
  .back .brand { position: absolute; left: 0; right: 0; top: 86px; justify-content: center; }
  .back .brand-name { font-size: 26px; letter-spacing: 2px; }
  .tagline {
    position: absolute; left: 0; right: 0; top: 140px;
    text-align: center; font-size: 14px; color: var(--ink-soft);
  }
  .address-band {
    position: absolute; left: 0; right: 0; bottom: 20px; height: 34px;
    background: var(--band-deep); color: var(--on-dark);
    display: flex; align-items: center; justify-content: center;
    font-size: 14px; letter-spacing: .3px;
  }
  .address-band::after {
    content: ""; position: absolute; left: 0; right: 0; bottom: -10px; height: 4px;
    background: var(--band-deep);
  }
</style>
</head>
<body>
<main class="canvas">

  <section class="card front" aria-label="Business card front">
    <svg class="front-swoosh" viewBox="0 0 525 300" aria-hidden="true">
      <defs>
        <linearGradient id="bandShade" x1="0" y1="0" x2="1" y2="1">
          <stop offset="0" stop-color="#2a292a"/>
          <stop offset="0.6" stop-color="#444243"/>
          <stop offset="1" stop-color="#1e1d1e"/>
        </linearGradient>
      </defs>
      <path d="M0 96 C160 216 330 271 525 278" fill="none" stroke="#2a292a" stroke-width="7"/>
      <path d="M0 110 C160 230 330 285 525 292 L525 300 L0 300 Z" fill="url(#bandShade)"/>
      <path d="M0 118 C160 238 330 291 525 298" fill="none" stroke="#ffffff" stroke-width="2.5"/>
    </svg>

    <div class="brand">
      <span class="brand-dot"></span>
      <span class="brand-name">Tallow Reed<br>Software</span>
    </div>

    <ul class="contact">
      <li>xxx xxxx xxxx
        <svg viewBox="0 0 12 12"><path d="M2.5 1h2l1 3-1.3 1a6 6 0 0 0 2.8 2.8l1-1.3 3 1v2a1 1 0 0 1-1 1A9.5 9.5 0 0 1 1.5 2a1 1 0 0 1 1-1z"/></svg>
      </li>
      <li>xxx xxxx xxxx
        <svg viewBox="0 0 12 12"><path d="M3.5 0h5a1 1 0 0 1 1 1v10a1 1 0 0 1-1 1h-5a1 1 0 0 1-1-1V1a1 1 0 0 1 1-1zm.5 1.5v8h4v-8z"/></svg>
      </li>
      <li>info@tallowreedsoftware.example
        <svg viewBox="0 0 12 12"><path d="M0 2h12v8H0zm1 1v.4l5 3.4 5-3.4V3z"/></svg>
      </li>
      <li>www.tallowreedsoftware.example
        <svg viewBox="0 0 12 12"><path d="M6 0a6 6 0 1 0 0 12A6 6 0 0 0 6 0zm0 1c.8.8 1.4 2.5 1.5 4.5h-3C4.6 3.5 5.2 1.8 6 1zM1.1 6.5h2.4c.1 1.6.5 3 1.1 4A5 5 0 0 1 1.1 6.5zm0-1a5 5 0 0 1 3.5-4c-.6 1-1 2.4-1.1 4zm3.4 1h3c-.1 2-.7 3.7-1.5 4.5-.8-.8-1.4-2.5-1.5-4.5zm4 0h2.4a5 5 0 0 1-3.5 4c.6-1 1-2.4 1.1-4zm0-1c-.1-1.6-.5-3-1.1-4a5 5 0 0 1 3.5 4z"/></svg>
      </li>
    </ul>

    <div class="person">
      <p class="person-name">Employee Name</p>
      <p class="person-title">Your Title</p>
    </div>
  </section>

  <section class="card back" aria-label="Business card back">
    <div class="brand">
      <span class="brand-dot"></span>
      <span class="brand-name">Tallow Reed Software</span>
    </div>
    <p class="tagline">See every device. Secure the network</p>
    <div class="address-band">4270 Vestridge Pond Blvd., Ste. 2600, Larkfield, MN 55812</div>
  </section>

</main>
</body>
</html>
```